WEBSITE DESIGN, VELTRA paint and panel

We are in need of a website for Veltra Paint & Panel based in Brisbane, Australia. We are a boutique Automotive Paint & Panel Company that provides services to all makes and models of vehicles. We have attached a logo that is still in draft stage but gives you an idea of the colour scheme and fonts and overall impact we are looking for. We are after a white background so this is clean and crisp whilst being sleek, modern and professional. The website must represent our slogan of Glowing finish on the Gleaming frame. The website must therefore be visually effective as our product is to get colour and placement on vehicle body's correct so the website must have this impact on our clients. We are after a widescreen webpage that is simple and logical to navigate. The final design should give clients the confidence that we can deliver on our promise.
Updates

Target Market(s)

Vehicle Owners who have a need for panel repairs and people who want to reinvigorate their car with a new coat of paint.

Industry/Entity Type

Car Repair

Coding

Coded - Design and coding required

Number of Pages Required

5+ page

Font styles to use
Sans Serif

Colors
ffffff
ffc214
000000

Requirements
Must have
• Page 1 - Home Page
• Page 2 - Our Process
• Page 3 - Private Customers
• Page 4 - Fleet & Corporate
• Page 5 - Insurance
• Page 6 - Get a Quote
• Page 7 - Connect (Contacts Page)
• Same font and colour scheme as the logo.
Should not have
• A typical mechanical/paint and panel layout which looks like a template website.

```html
<!DOCTYPE html>
<html lang="en">
<head>
<meta charset="utf-8">
<title>Veltra Paint &amp; Panel</title>
<link href="https://fonts.googleapis.com/css2?family=Open+Sans:wght@400;600;700&display=swap" rel="stylesheet">
<style>
:root{
  --ink:#1b1b1b;
  --header:#151515;
  --footer:#2a2a2a;
  --footer-bottom:#1e1e1e;
  --text:#555;
  --muted:#9a9a9a;
  --blue:#1f78c8;
  --blue-band:#2b86d6;
  --orange:#f7941d;
  --yellow:#ffc214;
  --white:#fff;
  --line:#3a3a3a;
}
*{box-sizing:border-box;margin:0;padding:0}
html,body{width:741px;height:1200px;overflow:hidden;background:var(--white)}
body{font-family:"Open Sans",Arial,sans-serif;color:var(--text);font-size:8px;line-height:1.5}
.wrap{width:620px;margin:0 auto;position:relative}

.site-header{height:70px;background:var(--header)}
.site-header .wrap{display:flex;align-items:center;justify-content:space-between;height:70px}
.brand{display:flex;align-items:center;gap:6px;color:var(--white);font-weight:700;font-size:11px;letter-spacing:1px;text-transform:uppercase}
.brand-mark{width:10px;height:10px;background:var(--yellow)}
.main-nav{display:flex;gap:16px}
.main-nav a{color:#ddd;text-decoration:none;font-size:7.5px}

.hero{height:375px;position:relative;background:linear-gradient(135deg,#cfd3d6 0%,#9aa2a8 35%,#3c4248 70%,#6f7a84 100%)}
.hero-caption{position:absolute;left:62px;bottom:58px;background:rgba(0,0,0,.7);color:var(--white);font-size:15px;font-weight:600;padding:6px 18px 6px 10px}
.hero-arrow{position:absolute;top:170px;width:22px;height:22px;border-radius:50%;background:rgba(0,0,0,.45);display:flex;align-items:center;justify-content:center}
.hero-arrow.prev{left:12px}
.hero-arrow.next{right:12px}

.welcome{padding-top:28px;text-align:center}
.section-title{font-size:17px;font-weight:700;color:var(--ink);letter-spacing:.5px}
.title-rule{width:40px;height:2px;background:var(--ink);margin:4px auto 8px}
.welcome p{font-size:7.5px;color:var(--text);max-width:600px;margin:0 auto}

.services{display:flex;gap:30px;margin-top:26px}
.service{display:flex;gap:10px;flex:1}
.service-photo{width:120px;height:96px;flex:none}
.service h3{font-size:13px;font-weight:600;color:var(--ink);margin-bottom:3px}
.service p{font-size:7px;margin-bottom:10px}
.btn-row{display:flex;gap:4px}
.btn{display:inline-block;font-size:6.5px;color:var(--white);padding:4px 10px;text-decoration:none}
.btn.primary{background:var(--blue)}
.btn.dark{background:var(--ink)}

.quote-band{margin-top:36px;height:66px;background:var(--blue-band);display:flex;align-items:center;justify-content:center;gap:20px}
.quote-band p{color:var(--white);font-size:14px}
.btn-quote{background:var(--orange);color:var(--white);font-size:8px;font-weight:600;padding:7px 20px;text-transform:uppercase;text-decoration:none}

.works{margin-top:30px}
.works-head{display:flex;justify-content:space-between;align-items:center;margin-bottom:10px}
.works-head .section-title{font-size:15px}
.works-nav{display:flex;gap:3px}
.works-grid{display:grid;grid-template-columns:repeat(4,1fr);gap:10px}
.work-photo{height:108px}

.site-footer{position:absolute;left:0;top:975px;width:741px;height:185px;background:var(--footer);color:var(--muted)}
.site-footer .wrap{display:grid;grid-template-columns:1fr 1fr 1fr 1fr;gap:22px;padding-top:22px}
.site-footer h4{color:var(--white);font-size:8px;font-weight:700;text-transform:uppercase;margin-bottom:8px}
.site-footer p,.site-footer li{font-size:6.5px}
.site-footer ul{list-style:none}
.site-footer li{padding:2px 0;border-bottom:1px solid var(--line)}
.contact-line{display:flex;gap:5px;align-items:center;margin-bottom:3px}
.field{height:14px;background:#3b3b3b;margin-bottom:5px;font-size:6px;color:#888;padding:2px 5px}
.field.area{height:22px}
.btn-submit{display:inline-block;background:var(--blue);color:var(--white);font-size:6px;padding:3px 10px;float:right}

.footer-bottom{position:absolute;left:0;top:1160px;width:741px;height:40px;background:var(--footer-bottom)}
.footer-bottom .wrap{display:flex;justify-content:space-between;align-items:center;height:40px;color:var(--muted);font-size:6.5px}
.social{display:flex;gap:6px}
.social span{width:9px;height:9px;border-radius:50%;background:#666}
</style>
</head>
<body>
<header class="site-header">
  <div class="wrap">
    <div class="brand"><span class="brand-mark"></span>Veltra paint and panel</div>
    <nav class="main-nav">
      <a href="#">Home</a><a href="#">Our Process</a><a href="#">Private Customers</a><a href="#">Fleet &amp; Corporate Accounts</a><a href="#">Get a Quote</a><a href="#">Contact</a>
    </nav>
  </div>
</header>

<section class="hero" role="img" aria-label="Smiling technician in blue overalls holding a spray gun in front of a dark car in the workshop">
  <div class="hero-caption">Glowing finish on the Gleaming frame</div>
  <span class="hero-arrow prev"><svg width="8" height="8" viewBox="0 0 8 8"><path d="M5.5 1 2.5 4l3 3" stroke="#fff" stroke-width="1.4" fill="none"/></svg></span>
  <span class="hero-arrow next"><svg width="8" height="8" viewBox="0 0 8 8"><path d="M2.5 1l3 3-3 3" stroke="#fff" stroke-width="1.4" fill="none"/></svg></span>
</section>

<main class="wrap">
  <section class="welcome">
    <h2 class="section-title">WELCOME</h2>
    <div class="title-rule"></div>
    <p>Veltra Paint &amp; Panel is a boutique Brisbane workshop restoring every make and model to a flawless finish. Our team matches colour precisely, repairs panels with care and returns each vehicle looking factory fresh. From small dents to complete resprays, we treat every car as our own and stand behind every job we deliver to our customers.</p>
  </section>

  <section class="services">
    <article class="service">
      <div class="service-photo" role="img" aria-label="Car being repaired on a workshop lift" style="background:linear-gradient(135deg,#4a4f55,#1d2024)"></div>
      <div>
        <h3>Panel Repairs</h3>
        <p>Dents, scratches and collision damage repaired by skilled technicians using modern tools and exact colour matching.</p>
        <div class="btn-row"><a class="btn primary" href="#">Read More</a><a class="btn dark" href="#">Request Service</a></div>
      </div>
    </article>
    <article class="service">
      <div class="service-photo" role="img" aria-label="Freshly painted red car in the spray booth" style="background:linear-gradient(135deg,#d9dde0,#8a2a2a)"></div>
      <div>
        <h3>Car Reinvigorate</h3>
        <p>Give your car a fresh new coat of paint with a deep, lasting gloss that turns heads on every road.</p>
        <div class="btn-row"><a class="btn dark" href="#">Read More</a><a class="btn dark" href="#">Request Service</a></div>
      </div>
    </article>
  </section>

  <section class="quote-band">
    <p>Ut laoreet dui elit, non eleifend nisl tempus quis.</p>
    <a class="btn-quote" href="#">Get a Quote</a>
  </section>

  <section class="works">
    <div class="works-head">
      <h2 class="section-title">OUR WORKS</h2>
      <div class="works-nav">
        <svg width="8" height="10" viewBox="0 0 8 10"><path d="M6 1 2 5l4 4" stroke="#1f78c8" stroke-width="1.6" fill="none"/></svg>
        <svg width="8" height="10" viewBox="0 0 8 10"><path d="M2 1l4 4-4 4" stroke="#1f78c8" stroke-width="1.6" fill="none"/></svg>
      </div>
    </div>
    <div class="works-grid">
      <div class="work-photo" role="img" aria-label="Technician fitting a wheel" style="background:linear-gradient(135deg,#6c737a,#23272b)"></div>
      <div class="work-photo" role="img" aria-label="Close view of a tyre and brake disc" style="background:linear-gradient(135deg,#3a3f44,#8d949a)"></div>
      <div class="work-photo" role="img" aria-label="Mechanic working on a wheel arch" style="background:linear-gradient(135deg,#9a8f86,#2e3236)"></div>
      <div class="work-photo" role="img" aria-label="Car raised on a hoist in the workshop" style="background:linear-gradient(135deg,#b3b8bd,#4a5056)"></div>
    </div>
  </section>
</main>

<footer class="site-footer">
  <div class="wrap">
    <div>
      <h4>Who we are</h4>
      <p>Veltra Paint &amp; Panel is a boutique automotive paint and panel company serving Brisbane drivers with quality workmanship, honest quotes and a finish built to last.</p>
    </div>
    <div>
      <h4>Useful links</h4>
      <ul><li>Home</li><li>Our Process</li><li>Private Customers</li><li>Fleet &amp; Corporate Accounts</li><li>Get a Quote</li><li>Contact</li></ul>
    </div>
    <div>
      <h4>Get in touch</h4>
      <p style="margin-bottom:6px">Call in or send us a message and our team will reply within one business day.</p>
      <div class="contact-line"><svg width="7" height="8" viewBox="0 0 7 8"><path d="M3.5 0a2.6 2.6 0 0 0-2.6 2.6C.9 4.6 3.5 8 3.5 8s2.6-3.4 2.6-5.4A2.6 2.6 0 0 0 3.5 0z" fill="#9a9a9a"/></svg>12 Kestrel Way, Brisbane QLD 4000</div>
      <div class="contact-line"><svg width="7" height="7" viewBox="0 0 7 7"><path d="M1.5 0l1.2 1.8-.7.8a4 4 0 0 0 2.4 2.4l.8-.7L7 5.5 5.8 7C2.6 6.7.3 4.4 0 1.2z" fill="#9a9a9a"/></svg>(07) 3555 0142</div>
      <div class="contact-line"><svg width="8" height="6" viewBox="0 0 8 6"><rect width="8" height="6" fill="#9a9a9a"/><path d="M0 0l4 3.2L8 0" stroke="#2a2a2a" fill="none"/></svg>hello@veltrapanel.com.au</div>
    </div>
    <div>
      <h4>Contact</h4>
      <div class="field">Name</div>
      <div class="field">Email</div>
      <div class="field area">Message</div>
      <span class="btn-submit">Submit</span>
    </div>
  </div>
</footer>
<div class="footer-bottom">
  <div class="wrap">
    <span>© 2024 Veltra Paint &amp; Panel. All rights reserved.</span>
    <div class="social"><span></span><span></span><span></span><span></span></div>
  </div>
</div>
</body>
</html>
```